Book cover design for a collection of poetry - The Lanternfield

Book cover and back design need to be moody, nostalgic, reflective, ethereal. Melancholy and other worldly. Cover design should not be time specific to a period or place but if applicable should reflect British landscape. Book cover should be in tones of blue and must include the title and author (THE LANTERNFIELD BY CORBIN WHITLACE). We love the idea of rain, and looking out of a window. See attached designs. A world you are observing but not in.

Industry/Entity Type

Book Publisher

Font styles to use
Serif
Script

Colors
3176b5
3377b5
85acd3
eaf1f7
0792cd
33a6d7
86cae7
ecf7fb
86cfc6

Requirements
Must have
• The colour blue in it, must be melancholy and reflective.
Nice to have
• Rain in the cover.
Should not have
• Any bright colours.

```html
<!DOCTYPE html>
<html lang="en">
<head>
<meta charset="utf-8">
<title>The Lanternfield — Cover and Back</title>
<link rel="stylesheet" href="https://fonts.googleapis.com/css2?family=Playfair+Display:wght@700;900&family=Montserrat:wght@400&display=swap">
<style>
  :root {
    --paper: #ffffff;
    --night: #0d1a44;
    --forest-deep: #03081a;
    --forest-mid: #123a8c;
    --title-shadow: #2f7fe0;
    --panel: #f4f8fa;
    --ornament-mid: #9fb0c2;
    --blurb: #12a6e4;
    --rule: #ffffff;
  }
  * { margin: 0; padding: 0; box-sizing: border-box; }
  html, body { width: 1200px; height: 820px; overflow: hidden; background: var(--paper); }
  .spread { position: relative; width: 1200px; height: 820px; background: var(--paper); }

  /* Front cover */
  .front { position: absolute; left: 0; top: 0; width: 586px; height: 820px; overflow: hidden; }
  .front-scene {
    position: absolute; inset: 0;
    background:
      radial-gradient(ellipse 45% 30% at 38% 62%, rgba(95,184,240,0.85), rgba(95,184,240,0) 70%),
      linear-gradient(180deg, #0b1f5c 0%, var(--forest-deep) 35%, #061240 60%, var(--forest-mid) 78%, #1c4f86 100%);
  }
  .title {
    position: absolute; left: 0; width: 586px; text-align: center;
    font-family: "Playfair Display", serif; font-weight: 900; color: var(--paper);
    text-shadow: 4px 3px 0 var(--title-shadow); line-height: 1; letter-spacing: 0.01em;
  }
  .title-the { top: 134px; font-size: 96px; }
  .title-main { top: 254px; font-size: 62px; letter-spacing: -0.01em; }
  .author-band {
    position: absolute; left: 0; top: 655px; width: 586px; height: 62px;
    border-top: 2px solid var(--rule); border-bottom: 2px solid var(--rule);
    display: flex; align-items: center; justify-content: center;
  }
  .author {
    font-family: "Playfair Display", serif; font-weight: 700; color: var(--paper);
    font-size: 34px; letter-spacing: 0.03em;
  }

  /* Back cover */
  .back { position: absolute; left: 614px; top: 0; width: 586px; height: 820px; background: var(--night); }
  .back-frame {
    position: absolute; left: 41px; top: 54px; width: 505px; height: 711px;
    border: 3px solid var(--rule); overflow: hidden;
  }
  .back-panel {
    position: absolute; left: 0; right: 0; top: 132px; height: 428px; background: var(--panel);
  }
  .ornament { position: absolute; left: 14px; right: 14px; }
  .ornament-top {
    top: 8px; height: 180px;
    background: linear-gradient(180deg, rgba(159,176,194,0) 0%, var(--ornament-mid) 55%, var(--panel) 100%);
  }
  .ornament-bottom {
    top: 505px; height: 195px;
    background: linear-gradient(0deg, rgba(159,176,194,0) 0%, var(--ornament-mid) 55%, var(--panel) 100%);
  }
  .blurb {
    position: absolute; left: 116px; right: 116px; top: 270px;
    font-family: "Montserrat", sans-serif; font-size: 12px; line-height: 16.8px;
    letter-spacing: 0.18em; word-spacing: -0.45em; color: var(--blurb);
    text-align: center; text-transform: uppercase;
  }
  .blurb p + p { margin-top: 16.8px; }
</style>
</head>
<body>
<main class="spread">
  <section class="front">
    <div class="front-scene" role="img" aria-label="Misty blue pine forest with light glowing between the trunks"></div>
    <h1 class="title title-the">THE</h1>
    <h1 class="title title-main">LANTERNFIELD</h1>
    <div class="author-band"><p class="author">CORBIN WHITLACE</p></div>
  </section>

  <section class="back">
    <div class="back-frame">
      <div class="back-panel"></div>
      <div class="ornament ornament-top" role="img" aria-label="White scrollwork ornament crowning the blurb panel"></div>
      <div class="ornament ornament-bottom" role="img" aria-label="White scrollwork ornament beneath the blurb panel"></div>
    </div>
    <div class="blurb">
      <p>The Lanternfield is a collection of poetry.</p>
      <p>Told in two parts we first meet Charles – aged, crippled and left alone in his inherited marsh house - reflecting on his life and his marriage to beautiful Alice who we meet in part two. Alice is suicidal, manically depressed and struggling with life as a wife and mother. She meets, harbors and falls in love with a soldier during WWII and her world is changed forever.</p>
      <p>Moving through the 20th century, this life and the next, The Lanternfield interweaves grief, loss, the after-life, mental illness, and ultimately the true nature of love.</p>
    </div>
  </section>
</main>
</body>
</html>
```